Redesign Digital Lending Mobile App - Android/ Flutter

Want to re-theme an existing Digital Lending Mobile app to simplify customer journeys, as well as uplift the UI.

Most users will have small screen phones so the design needs to take that into consideration while also adapting to those with larger devices, like admins with Tablets.

Have already laid out customer journeys on Figma with guidance on how the flow of the app should be. https://www.plankora.example/board/q4ZtRm81KdWe7YhXcvBnaL/LoomKit?frame-id=3-5182&s=Jk2pQwEr7TyUi-9

Video capture of current app: https://vaultbin.example/clip/7Hx3LmQp9RtZw2KcVn4YsBd8EfGj1/play
https://vaultbin.example/clip/4PsWq8ZnTk2LrXy6MbJc3VhGd9FeA/play

The documented views for Web are also here https://docshelf.example/open?ref=3B8F2204AD7C91E5!tk8d1f6a2c4e7b90d3f5a1c8e2b6d4f9a07&cid=3b8f2204ad7c91e5&kind=file%2Cdocx&wdo=2

Target Market(s)

Kenya, Tanzania, Uganda - Africa

Industry/Entity Type

Fintech

Requirements
Must have
• Responsive for diff screens, esp. in context of smaller screen smartphone
Nice to have
• Thematic components to ensure new views can easily be adapted to these themse

```html
<!DOCTYPE html>
<html lang="en">
<head>
<meta charset="utf-8">
<title>LoomKit – Lending App Screens</title>
<link href="https://fonts.googleapis.com/css2?family=Lato:wght@400;700;900&display=swap" rel="stylesheet">
<style>
:root{
  --bg:#dcdcdc;
  --screen:#f3f5fa;
  --white:#ffffff;
  --blue:#3478c8;
  --green:#4a9e68;
  --ink:#1d1f24;
  --track:#dce5f6;
  --line:#e2e5ec;
  --muted:#b3c1d9;
  --pill:#dde8f8;
}
*{box-sizing:border-box;margin:0;padding:0}
html,body{width:1200px;height:781px;overflow:hidden;background:var(--bg);font-family:'Lato',sans-serif;color:var(--ink)}
.stage{position:absolute;left:0;top:0;width:1536px;height:1000px;transform:scale(0.78125);transform-origin:0 0}
.phone{position:absolute;top:78px;height:844px;background:var(--screen);border-radius:42px;overflow:hidden;box-shadow:0 2px 10px rgba(0,0,0,.06)}
.phone--home{left:94px;width:392px}
.phone--summary{left:574px;width:388px}
.phone--report{left:1056px;width:388px}
.abs{position:absolute}
.divider{position:absolute;height:1px;background:var(--line)}
.ring{position:absolute;width:38px;height:38px;border:2px solid var(--blue);border-radius:50%;display:flex;align-items:center;justify-content:center;background:var(--white)}
.ring svg{width:20px;height:20px}
.brand-mark{position:absolute;left:36px;top:20px;width:42px;height:42px;border-radius:50%;background:var(--blue)}
.brand-name{position:absolute;left:21px;top:70px;font-size:19px;font-weight:900;color:var(--blue);letter-spacing:.3px}
.stat{position:absolute;top:137px;width:80px;height:46px;background:var(--blue);border-radius:6px;color:var(--white);font-size:10px;line-height:18px;padding:5px 0 0 9px;box-shadow:0 2px 4px rgba(52,120,200,.3)}
.section-title{position:absolute;font-size:16px;font-weight:400}
.chip{position:absolute;height:35px;background:var(--green);color:var(--white);font-size:12.5px;border-radius:5px;display:flex;align-items:center;justify-content:center;gap:6px;box-shadow:0 2px 4px rgba(0,0,0,.15)}
.chip::after{content:"";border:3.5px solid transparent;border-top:4px solid var(--white);margin-top:4px}
.metric{position:absolute;left:21px;width:352px;display:flex;justify-content:space-between;font-size:14.5px}
.track{position:absolute;left:21px;width:352px;height:8px;border-radius:4px;background:var(--track)}
.track span{display:block;width:122px;height:100%;border-radius:4px;background:var(--blue)}
.bar{position:absolute;bottom:0}
.bar--blue{background:var(--blue)}
.bar--green{background:var(--green)}
.tick{position:absolute;font-size:7px;color:#444;transform:translateX(-50%)}
.btn-next{position:absolute;background:linear-gradient(90deg,var(--green),var(--blue));color:var(--white);border-radius:22px;display:flex;align-items:center;justify-content:center;box-shadow:0 3px 5px rgba(0,0,0,.25)}
.title{position:absolute;font-size:22px;font-weight:700;color:var(--blue)}
.title--grad{background:linear-gradient(90deg,var(--blue),var(--green));-webkit-background-clip:text;background-clip:text;color:transparent}
.nav{position:absolute;left:0;right:0;top:754px;height:90px;background:var(--white);border-top:1px solid #eceef2}
.nav-item{position:absolute;top:18px;width:70px;margin-left:-35px;text-align:center;font-size:12px;color:var(--muted)}
.nav-item svg{display:block;margin:0 auto 6px;width:26px;height:26px}
.nav-item--active{color:var(--blue);font-weight:700}
.detail-table{position:absolute;left:53px;top:229px;width:280px;border-collapse:collapse;font-size:12px;box-shadow:0 2px 10px rgba(0,0,0,.08);background:var(--white)}
.detail-table td{height:45.6px;padding-left:13px}
.detail-table td+td{border-left:1px solid var(--line);padding-left:20px}
.detail-table tr:nth-child(even) td{background:#f5f6f8}
.toggle{position:absolute;top:240px;height:42px;border-radius:21px;display:flex;align-items:center;justify-content:center;font-size:18px}
.toggle--on{left:82px;width:110px;background:linear-gradient(90deg,var(--green),var(--blue));color:var(--white);box-shadow:0 3px 5px rgba(0,0,0,.25)}
.toggle--off{left:216px;width:90px;background:var(--pill);color:var(--blue)}
.period{position:absolute;top:317px;font-size:16px;color:var(--blue);height:34px;line-height:34px;transform:translateX(-50%)}
.period--on{background:var(--pill);border-radius:17px;width:76px;text-align:center}
.card{position:absolute;width:166px;height:50px;background:var(--blue);border-radius:6px;color:var(--white);font-size:15px;display:flex;align-items:center;justify-content:space-between;padding:0 12px 0 13px}
.card svg{width:26px;height:26px}
</style>
</head>
<body>
<div class="stage">

  <!-- Home screen -->
  <section class="phone phone--home">
    <div class="brand-mark"></div>
    <div class="brand-name">LoomKit</div>
    <div class="ring" style="left:222px;top:37px"><svg viewBox="0 0 24 24" fill="var(--green)"><path d="M12 3 2 12h3v8h5v-5h4v5h5v-8h3z"/></svg></div>
    <div class="ring" style="left:279px;top:37px"><svg viewBox="0 0 24 24" fill="var(--blue)"><circle cx="12" cy="8" r="4"/><path d="M4 21c0-5 4-7 8-7s8 2 8 7z"/></svg></div>
    <div class="ring" style="left:335px;top:37px"><svg viewBox="0 0 24 24" fill="var(--blue)"><path d="M12 22a2.5 2.5 0 0 0 2.5-2.5h-5A2.5 2.5 0 0 0 12 22zm7-5-1.5-2V10a5.5 5.5 0 0 0-11 0v5L5 17v1h14z"/><circle cx="17" cy="6" r="3.5" fill="var(--green)"/></svg></div>
    <div class="divider" style="left:21px;top:111px;width:352px"></div>

    <div class="stat" style="left:21px">0 Disbursed<br>$ 30,000</div>
    <div class="stat" style="left:111px">0 Collected<br>$ 20,000</div>
    <div class="stat" style="left:202px">0 Active Client<br>$ 50</div>
    <div class="stat" style="left:292px">0 New Clients<br>$ 30</div>

    <div class="section-title" style="left:21px;top:209px">Filters</div>
    <div class="chip" style="left:21px;top:242px;width:100px">Loan Officer</div>
    <div class="chip" style="left:134px;top:242px;width:71px">Branch</div>
    <div class="chip" style="left:219px;top:242px;width:58px">Fund</div>
    <div class="chip" style="left:293px;top:242px;width:80px">Product</div>

    <div class="metric" style="top:302px"><span>Near Due</span><span>$ 25, 00, 000</span></div>
    <div class="track" style="top:335px"><span></span></div>
    <div class="metric" style="top:361px"><span>Due</span><span>$ 34, 000</span></div>
    <div class="track" style="top:394px"><span></span></div>
    <div class="metric" style="top:419px"><span>Pending Disbursement</span><span>$ 30, 000</span></div>
    <div class="track" style="top:452px"><span></span></div>
    <div class="metric" style="top:478px"><span>Active Loan</span><span>$ 20, 000</span></div>
    <div class="track" style="top:511px"><span></span></div>
    <div class="divider" style="left:21px;top:550px;width:352px"></div>

    <div class="section-title" style="left:21px;top:572px">Reports</div>
    <div class="abs" style="left:21px;top:580px;width:243px;height:134px;border-bottom:1px solid #ccd">
      <div class="bar bar--blue" style="left:8px;width:22px;height:61px"></div>
      <div class="bar bar--blue" style="left:48px;width:22px;height:82px"></div>
      <div class="bar bar--blue" style="left:90px;width:22px;height:36px"></div>
      <div class="bar bar--blue" style="left:131px;width:22px;height:42px"></div>
      <div class="bar bar--green" style="left:171px;width:22px;height:83px"></div>
      <div class="bar bar--green" style="left:214px;width:22px;height:113px"></div>
    </div>
    <div class="tick" style="left:40px;top:718px">F1</div>
    <div class="tick" style="left:79px;top:718px">F2</div>
    <div class="tick" style="left:123px;top:718px">F3</div>
    <div class="tick" style="left:163px;top:718px">F4</div>
    <div class="tick" style="left:203px;top:718px">F5</div>
    <div class="tick" style="left:246px;top:718px">F6</div>
    <div class="btn-next" style="left:294px;top:693px;width:78px;height:29px;font-size:14px">Next</div>

    <nav class="nav">
      <div class="nav-item nav-item--active" style="left:38px"><svg viewBox="0 0 24 24" fill="var(--green)"><path d="M12 3 2 12h3v8h5v-5h4v5h5v-8h3z"/></svg>Home</div>
      <div class="nav-item" style="left:115px"><svg viewBox="0 0 24 24" fill="var(--muted)"><circle cx="10" cy="5" r="2.5"/><path d="M4 14a6 6 0 0 1 12 0v4H4z"/><circle cx="17" cy="18" r="4.5" fill="#c9d3e5"/></svg>Loans</div>
      <div class="nav-item" style="left:193px"><svg viewBox="0 0 24 24" fill="var(--muted)"><path d="M5 2h10l4 4v16H5z"/><path d="M8 10h8M8 14h8M8 18h5" stroke="#fff" stroke-width="1.6"/></svg>Summary</div>
      <div class="nav-item" style="left:271px"><svg viewBox="0 0 24 24" fill="var(--muted)"><path d="M5 2h14v20H5z"/><path d="M9 18v-4M12 18v-7M15 18v-9" stroke="#fff" stroke-width="2"/></svg>Report</div>
      <div class="nav-item" style="left:349px"><svg viewBox="0 0 24 24" fill="none" stroke="var(--muted)" stroke-width="2.4"><circle cx="12" cy="12" r="7"/><circle cx="12" cy="12" r="2.5"/></svg>Settings</div>
    </nav>
  </section>

  <!-- Loan summary screen -->
  <section class="phone phone--summary">
    <div class="title title--grad" style="left:17px;top:33px">Loan Summary</div>
    <div class="ring" style="left:274px;top:30px"><svg viewBox="0 0 24 24" fill="var(--green)"><path d="M5 2h10l4 4v16H5z"/><path d="M8 10h8M8 14h8M8 18h5" stroke="#fff" stroke-width="1.6"/></svg></div>
    <div class="ring" style="left:331px;top:30px"><svg viewBox="0 0 24 24" fill="none" stroke="var(--blue)" stroke-width="2.6"><circle cx="10.5" cy="10.5" r="6"/><path d="M15 15l5 5"/></svg></div>
    <div class="divider" style="left:17px;top:94px;width:353px"></div>

    <div class="section-title" style="left:18px;top:121px">Filters</div>
    <div class="chip" style="left:18px;top:154px;width:100px">Loan Officer</div>
    <div class="chip" style="left:131px;top:154px;width:71px">Branch</div>
    <div class="chip" style="left:216px;top:154px;width:58px">Fund</div>
    <div class="chip" style="left:290px;top:154px;width:80px">Product</div>

    <table class="detail-table">
      <colgroup><col style="width:178px"><col></colgroup>
      <tr><td>Loan reference No 1</td><td>3213</td></tr>
      <tr><td>Loan status</td><td>Active</td></tr>
      <tr><td>Date Disbursed</td><td>13 Jul 2024</td></tr>
      <tr><td>Data Approved</td><td>20 Jul 2024</td></tr>
      <tr><td>Last repayment date</td><td>27 Jul 2024</td></tr>
      <tr><td>Next repayment date</td><td>27 Jul 2024</td></tr>
      <tr><td>Amount Disbursed</td><td>$30,000</td></tr>
      <tr><td>Amount outstanding</td><td>$30,000</td></tr>
      <tr><td>Overdue Days</td><td>30</td></tr>
    </table>

    <div class="btn-next" style="left:138px;top:679px;width:110px;height:43px;font-size:18px">Next</div>

    <nav class="nav">
      <div class="nav-item" style="left:35px"><svg viewBox="0 0 24 24" fill="var(--muted)"><path d="M12 3 2 12h3v8h5v-5h4v5h5v-8h3z"/></svg>Home</div>
      <div class="nav-item" style="left:112px"><svg viewBox="0 0 24 24" fill="var(--muted)"><circle cx="10" cy="5" r="2.5"/><path d="M4 14a6 6 0 0 1 12 0v4H4z"/><circle cx="17" cy="18" r="4.5" fill="#c9d3e5"/></svg>Loans</div>
      <div class="nav-item nav-item--active" style="left:190px"><svg viewBox="0 0 24 24" fill="var(--green)"><path d="M5 2h10l4 4v16H5z"/><path d="M8 10h8M8 14h8M8 18h5" stroke="#fff" stroke-width="1.6"/></svg>Summary</div>
      <div class="nav-item" style="left:268px"><svg viewBox="0 0 24 24" fill="var(--muted)"><path d="M5 2h14v20H5z"/><path d="M9 18v-4M12 18v-7M15 18v-9" stroke="#fff" stroke-width="2"/></svg>Report</div>
      <div class="nav-item" style="left:346px"><svg viewBox="0 0 24 24" fill="none" stroke="var(--muted)" stroke-width="2.4"><circle cx="12" cy="12" r="7"/><circle cx="12" cy="12" r="2.5"/></svg>Settings</div>
    </nav>
  </section>

  <!-- Report screen -->
  <section class="phone phone--report">
    <div class="title" style="left:18px;top:32px">Report</div>
    <div class="ring" style="left:331px;top:28px"><svg viewBox="0 0 24 24" fill="var(--green)"><path d="M5 2h14v20H5z"/><path d="M9 18v-4M12 18v-7M15 18v-9" stroke="#fff" stroke-width="2"/></svg></div>
    <div class="divider" style="left:18px;top:92px;width:352px"></div>

    <div class="title title--grad" style="left:0;width:390px;text-align:center;top:120px;font-size:26px">Total loan $35,00,000</div>

    <div class="chip" style="left:19px;top:176px;width:100px">Loan Officer</div>
    <div class="chip" style="left:132px;top:176px;width:71px">Branch</div>
    <div class="chip" style="left:217px;top:176px;width:58px">Fund</div>
    <div class="chip" style="left:291px;top:176px;width:80px">Product</div>

    <div class="toggle toggle--on">Profit</div>
    <div class="toggle toggle--off">Loss</div>

    <div class="period" style="left:39px">Day</div>
    <div class="period" style="left:144px">Week</div>
    <div class="period period--on" style="left:250px">Month</div>
    <div class="period" style="left:354px">Year</div>

    <div class="abs" style="left:47px;top:370px;width:295px;height:187px;border-bottom:1px solid #ccd">
      <div class="bar bar--blue" style="left:12px;width:31px;height:84px"></div>
      <div class="bar bar--blue" style="left:91px;width:31px;height:113px"></div>
      <div class="bar bar--blue" style="left:172px;width:31px;height:50px"></div>
      <div class="bar bar--green" style="left:252px;width:31px;height:179px"></div>
    </div>
    <div class="tick" style="left:74px;top:563px;font-size:8px">Week 1</div>
    <div class="tick" style="left:150px;top:563px;font-size:8px">Week 2</div>
    <div class="tick" style="left:235px;top:563px;font-size:8px">Week 3</div>
    <div class="tick" style="left:316px;top:563px;font-size:8px">Week 4</div>

    <div class="card" style="left:19px;top:603px">Revenue $300
      <svg viewBox="0 0 24 24" fill="var(--white)"><circle cx="12" cy="6" r="4"/><path d="M2 14l5 6h10l5-6-3-1-4 3H8l-3-3z"/></svg></div>
    <div class="card" style="left:196px;top:603px">Expenses $350
      <svg viewBox="0 0 24 24" fill="var(--white)"><rect x="2" y="8" width="18" height="13" rx="2"/><path d="M6 8l9-5 2 5z"/></svg></div>
    <div class="card" style="left:19px;top:671px">Tax $200
      <svg viewBox="0 0 24 24" fill="var(--white)"><rect x="4" y="2" width="14" height="20" rx="2"/><circle cx="17" cy="16" r="5" fill="var(--white)" stroke="var(--blue)" stroke-width="1.5"/></svg></div>
    <div class="card" style="left:196px;top:671px">Salaries $3500
      <svg viewBox="0 0 24 24" fill="var(--white)"><rect x="2" y="6" width="20" height="14" rx="2"/><circle cx="12" cy="13" r="3" fill="var(--blue)"/></svg></div>

    <nav class="nav">
      <div class="nav-item" style="left:37px"><svg viewBox="0 0 24 24" fill="var(--muted)"><path d="M12 3 2 12h3v8h5v-5h4v5h5v-8h3z"/></svg>Home</div>
      <div class="nav-item" style="left:113px"><svg viewBox="0 0 24 24" fill="var(--muted)"><circle cx="10" cy="5" r="2.5"/><path d="M4 14a6 6 0 0 1 12 0v4H4z"/><circle cx="17" cy="18" r="4.5" fill="#c9d3e5"/></svg>Loans</div>
      <div class="nav-item" style="left:191px"><svg viewBox="0 0 24 24" fill="var(--muted)"><path d="M5 2h10l4 4v16H5z"/><path d="M8 10h8M8 14h8M8 18h5" stroke="#fff" stroke-width="1.6"/></svg>Summary</div>
      <div class="nav-item nav-item--active" style="left:269px"><svg viewBox="0 0 24 24" fill="var(--green)"><path d="M5 2h14v20H5z"/><path d="M9 18v-4M12 18v-7M15 18v-9" stroke="#fff" stroke-width="2"/></svg>Report</div>
      <div class="nav-item" style="left:347px"><svg viewBox="0 0 24 24" fill="none" stroke="var(--muted)" stroke-width="2.4"><circle cx="12" cy="12" r="7"/><circle cx="12" cy="12" r="2.5"/></svg>Settings</div>
    </nav>
  </section>

</div>
</body>
</html>
```